Business Card for Coastal Tundrabridge Advisory

We need a business card for Coastal Tundrabridge Advisory. The company website address is provided below. The company logo is attached. We provide specialized permafrost services to the mining, transportation, and oil & gas industries. The card should be prepared for:
Matthias Korhonen, PhD.
Coastal Tundrabridge Advisory
PO Box 418259
Quillwater, Alaska 99642
Direct: +1-907-555-0143
Email: mkorhonen@tundrabridgeadvisory.example
Website: www.coastaltundrabridgeadvisory.example

```html
<!DOCTYPE html>
<html lang="en">
<head>
<meta charset="utf-8">
<title>Coastal Tundrabridge Advisory – Business Card</title>
<link rel="stylesheet" href="https://fonts.googleapis.com/css2?family=Roboto+Condensed:wght@400;700&display=swap">
<style>
  :root {
    --canvas: #eeeeef;
    --card-front: #ffffff;
    --ink: #1a1a1a;
    --icon-bg: #8a8a8a;
    --icon-fg: #ffffff;
    --back-dark: #2b2b2b;
    --back-mid: #3a3a3a;
    --back-light: #4a4a4a;
    --brand-light: #f4f4f4;
  }
  * { box-sizing: border-box; margin: 0; padding: 0; }
  html, body {
    width: 1200px; height: 1200px; overflow: hidden;
    background: var(--canvas);
    font-family: "Roboto Condensed", "Arial Narrow", sans-serif;
    color: var(--ink);
  }
  .card {
    position: absolute;
    left: 237px;
    width: 725px;
    height: 412px;
    border-radius: 28px;
    overflow: hidden;
  }
  .card-front { top: 150px; background: var(--card-front); }
  .card-back { top: 650px; }

  .brand-name {
    position: absolute;
    left: 44px; top: 168px;
    width: 300px;
    font-weight: 700;
    font-size: 30px;
    line-height: 1.05;
    letter-spacing: 1.5px;
    text-transform: uppercase;
    color: var(--ink);
  }
  .details {
    position: absolute;
    left: 382px; top: 76px;
  }
  .person-name {
    font-weight: 700;
    font-size: 23px;
    text-transform: uppercase;
    letter-spacing: 0.2px;
  }
  .person-title { font-size: 16px; margin-top: 2px; }
  .contact-list {
    list-style: none;
    margin-top: 34px;
    position: relative;
  }
  .contact-list::before {
    content: "";
    position: absolute;
    left: 0; top: 0;
    width: 26px; height: 116px;
    background: var(--icon-bg);
    border-radius: 5px;
  }
  .contact-item {
    position: relative;
    display: flex; align-items: center;
    height: 29px;
    font-size: 17px;
  }
  .contact-icon { width: 26px; height: 18px; flex: none; margin-right: 18px; }
  .address { margin-top: 38px; font-size: 17px; line-height: 1.4; }

  .back-pattern {
    position: absolute; inset: 0;
    background: linear-gradient(160deg, var(--back-mid) 0%, var(--back-dark) 45%, var(--back-light) 75%, var(--back-dark) 100%);
  }
  .back-brand {
    position: absolute;
    left: 330px; top: 232px;
    width: 340px;
    font-weight: 700;
    font-size: 30px;
    line-height: 1.05;
    letter-spacing: 1.5px;
    text-transform: uppercase;
    color: var(--brand-light);
  }
</style>
</head>
<body>

<section class="card card-front" aria-label="Card front">
  <div class="brand-name">Coastal Tundrabridge Advisory</div>

  <div class="details">
    <h1 class="person-name">Matthias Korhonen, PhD</h1>
    <p class="person-title">Founder &amp; Director</p>

    <ul class="contact-list">
      <li class="contact-item">
        <svg class="contact-icon" viewBox="0 0 26 18" aria-hidden="true">
          <path d="M9 4c1-1 2 0 2.5 1l.8 1.6c.3.6 0 1.2-.5 1.5l-.6.4c.6 1.3 1.6 2.3 2.9 2.9l.4-.6c.3-.5 1-.8 1.5-.5l1.6.8c1 .5 2 1.5 1 2.5-2 2-8.5-1-9.6-5.5C8.5 6.6 8.5 4.5 9 4z" fill="var(--icon-fg)"/>
        </svg>
        <span>+1-907-555-0143</span>
      </li>
      <li class="contact-item">
        <svg class="contact-icon" viewBox="0 0 26 18" aria-hidden="true">
          <rect x="10" y="3" width="6.5" height="12" rx="1.2" fill="none" stroke="var(--icon-fg)" stroke-width="1.4"/>
          <circle cx="13.25" cy="12.8" r="0.8" fill="var(--icon-fg)"/>
        </svg>
        <span>(907) 555 0178</span>
      </li>
      <li class="contact-item">
        <svg class="contact-icon" viewBox="0 0 26 18" aria-hidden="true">
          <rect x="8.5" y="5" width="9" height="7" fill="var(--icon-fg)"/>
          <path d="M8.5 5l4.5 4 4.5-4" fill="none" stroke="var(--icon-bg)" stroke-width="1"/>
        </svg>
        <span>mkorhonen@tundrabridgeadvisory.example</span>
      </li>
      <li class="contact-item">
        <svg class="contact-icon" viewBox="0 0 26 18" aria-hidden="true">
          <circle cx="13" cy="9" r="5" fill="none" stroke="var(--icon-fg)" stroke-width="1.3"/>
          <ellipse cx="13" cy="9" rx="2" ry="5" fill="none" stroke="var(--icon-fg)" stroke-width="1"/>
          <path d="M8 9h10" stroke="var(--icon-fg)" stroke-width="1"/>
        </svg>
        <span>www.coastaltundrabridgeadvisory.example</span>
      </li>
    </ul>

    <p class="address">PO Box 418259<br>Quillwater, Alaska 99642</p>
  </div>
</section>

<section class="card card-back" aria-label="Card back">
  <div class="back-pattern" role="img" aria-label="Dark background with a tone-on-tone repeated company name pattern"></div>
  <div class="back-brand">Coastal Tundrabridge Advisory</div>
</section>

</body>
</html>
```